Flat Belly Design Graphics for Social

I want to create 9 social media graphics (new Instagram size 4:5 (1080 x 1350 pixels) focusing on our Flat Belly Graphics, using the pics attached. Use the attached pics, NO RANDOM STOCK PHOTOGRAPHY. For the color scheme of the graphics, the color palette is attached. YOU MUST POST ALL 9 GRAPHICS IN ONE ENTRY.
Using the 3 titles below, create one set of graphics. 1) with all text, then for the others, use the pictures as detailed below in IMPORTANT:
1. Ten-Week Bright Morning Reboot
2. The Quick Garden Kitchen Menu Guide
3. Studio Habits for Lasting Energy Past Midlife - Zero Gym Needed
IMPORTANT:
Only use RK Pic 1 and RK Pic 2 with the title, Ten-Week Bright Morning Reboot
Only use meal plan1 and meal plan2 pics with the title, Quick Garden Kitchen Menu Guide
Only use studio habits 1 and studio habits 2 pics with the title, Studio Habits for Lasting Energy Past Midlife - Zero Gym Needed
women over 40

```html
<!DOCTYPE html>
<html lang="en">
<head>
<meta charset="utf-8">
<title>Morning Reboot Social Set</title>
<link rel="stylesheet" href="https://fonts.googleapis.com/css2?family=Oswald:wght@500;600;700&display=swap">
<style>
:root{
  --backdrop:#240d14;
  --cream:#fbeeee;
  --forest:#334e4c;
  --rose:#d97d9a;
  --rose-mid:#e196b0;
  --blush:#f6d2de;
  --teal:#5fb2a5;
  --white:#ffffff;
}
*{margin:0;padding:0;box-sizing:border-box}
html,body{width:1074px;height:1200px;overflow:hidden;background:var(--backdrop)}
body{position:relative;font-family:'Oswald',sans-serif;font-weight:700;line-height:1}
.tile{position:absolute;width:259px;height:324px;overflow:hidden}
.col-1{left:122px}.col-2{left:408px}.col-3{left:693px}
.row-1{top:94px}.row-2{top:438px}.row-3{top:782px}
.abs{position:absolute}
.line{display:block;white-space:nowrap}
.card{position:absolute;left:14px;top:15px;width:231px;height:294px;border-radius:24px;background:var(--forest)}
.photo{position:absolute}
.bar{display:block;white-space:nowrap;text-align:center}
.blob{position:absolute;left:0;width:259px}
</style>
</head>
<body>

<!-- Row 1: text-only covers -->
<section class="tile col-1 row-1" style="background:var(--cream)">
  <div class="card">
    <div class="abs" style="left:22px;top:44px;color:var(--white)">
      <span class="line" style="font-size:28px;color:var(--rose);font-weight:600">TEN-WEEK</span>
      <span class="line" style="font-size:48px;margin-top:6px">BRIGHT</span>
      <span class="line" style="font-size:48px;margin-top:4px">MORNING</span>
      <span class="line" style="font-size:38px;font-weight:600;margin-top:8px">Reboot</span>
    </div>
  </div>
</section>

<section class="tile col-2 row-1" style="background:var(--cream)">
  <div class="card">
    <div class="abs" style="left:0;width:231px;top:28px;text-align:center;color:var(--white)">
      <span class="line" style="font-size:28px;font-weight:600">The Quick</span>
      <span class="line" style="font-size:62px;color:var(--rose);margin-top:4px">Garden</span>
      <span class="line" style="font-size:52px;color:var(--rose);margin-top:4px">KITCHEN</span>
      <span class="line" style="font-size:38px;font-weight:600;margin-top:12px">Menu Guide</span>
    </div>
  </div>
</section>

<section class="tile col-3 row-1" style="background:var(--cream)">
  <div class="card">
    <div class="abs" style="left:22px;top:24px;color:var(--white)">
      <span class="line" style="font-size:17px;color:var(--rose);font-weight:600">Studio Habits for</span>
      <span class="line" style="font-size:50px;margin-top:6px">LASTING</span>
      <span class="line" style="font-size:50px;margin-top:4px">ENERGY</span>
      <span class="line" style="font-size:32px;color:var(--rose);margin-top:10px">PAST MIDLIFE</span>
      <span class="line" style="font-size:22px;font-weight:600;margin-top:8px">Zero Gym Needed</span>
    </div>
  </div>
</section>

<!-- Row 2 -->
<section class="tile col-1 row-2" style="background:var(--forest)">
  <div class="abs" style="left:81px;top:0;width:97px;height:210px;background:var(--blush)"></div>
  <div class="photo" role="img" aria-label="Smiling woman in a white cropped sweater pointing at her waist" style="left:55px;top:20px;width:150px;height:200px;border-radius:60px 60px 8px 8px;background:linear-gradient(180deg,#4a2f27 0%,#f1ede9 40%,#e9e3df 65%,#1c1c1f 100%)"></div>
  <svg class="blob" style="top:198px;height:126px" viewBox="0 0 259 126" preserveAspectRatio="none" aria-hidden="true">
    <path d="M10 18 L60 4 L110 14 L160 2 L215 10 L250 4 L246 40 L258 70 L244 100 L252 122 L190 114 L130 124 L70 112 L20 122 L0 96 L12 66 L2 40 Z" fill="var(--blush)"/>
  </svg>
  <div class="abs" style="left:0;width:259px;top:222px;text-align:center">
    <span class="line" style="font-size:19px;color:var(--teal);font-weight:600">Ten-Week</span>
    <span class="line" style="font-size:29px;color:var(--forest);margin-top:5px">BRIGHT MORNING</span>
    <span class="bar" style="margin:7px auto 0;width:195px;height:23px;background:var(--rose-mid);color:var(--forest);font-size:19px;letter-spacing:4px;line-height:23px">Reboot</span>
  </div>
</section>

<section class="tile col-2 row-2" style="background:var(--white)">
  <div class="photo" role="img" aria-label="Overhead spread of chicken, fruit, vegetables, grains and a meal planner on dark wood" style="left:13px;top:9px;width:231px;height:155px;background:linear-gradient(135deg,#e8b7a5 0%,#6b4a36 45%,#b63a3a 70%,#7c5a3a 100%)"></div>
  <div class="abs" style="left:0;top:173px;width:259px;height:151px;background:var(--forest)"></div>
  <div class="abs" style="left:11px;top:191px;width:237px;height:120px;background:var(--rose-mid);text-align:center;padding-top:14px">
    <span class="line" style="font-size:20px;color:var(--white);font-weight:600">The Quick</span>
    <span class="line" style="font-size:28px;color:var(--forest);margin-top:8px">GARDEN KITCHEN</span>
    <span class="bar" style="margin:9px auto 0;width:195px;height:23px;background:var(--blush);color:var(--forest);font-size:19px;letter-spacing:4px;line-height:23px">Menu Guide</span>
  </div>
</section>

<section class="tile col-3 row-2" style="background:var(--forest)">
  <div class="photo" role="img" aria-label="Two women sharing a secret, one whispering and the other looking surprised" style="left:13px;top:12px;width:233px;height:154px;background:linear-gradient(135deg,#eef0f2 0%,#b98a72 45%,#3b2a24 70%,#f3f1ef 100%)"></div>
  <svg class="blob" style="top:170px;height:154px" viewBox="0 0 259 154" preserveAspectRatio="none" aria-hidden="true">
    <path d="M8 16 L70 2 L130 12 L190 0 L250 10 L246 46 L259 82 L248 120 L226 150 L160 140 L100 154 L40 142 L4 150 L12 110 L0 70 L10 40 Z" fill="var(--blush)"/>
  </svg>
  <div class="abs" style="left:0;width:259px;top:196px;text-align:center">
    <span class="line" style="font-size:20px;color:var(--teal);font-weight:600">Studio Habits for Lasting</span>
    <span class="line" style="font-size:38px;color:var(--forest);margin-top:4px">ENERGY PAST</span>
    <span class="bar" style="margin:6px auto 0;width:206px;height:23px;background:var(--rose-mid);color:var(--white);font-size:15px;font-weight:600;line-height:23px">Midlife - Zero Gym Needed</span>
  </div>
</section>

<!-- Row 3 -->
<section class="tile col-1 row-3" style="background:var(--forest)">
  <svg class="abs" style="left:0;top:0" width="259" height="324" viewBox="0 0 259 324" aria-hidden="true">
    <polygon points="54,324 259,138 259,324" fill="var(--rose-mid)"/>
  </svg>
  <div class="photo" role="img" aria-label="Smiling woman in a white cropped sweater standing in a kitchen, pointing at her waist" style="left:0;top:0;width:135px;height:324px;background:linear-gradient(180deg,#5a3f31 0%,#8a6b55 25%,#efebe7 50%,#e5dfda 68%,#1b1b1e 100%)"></div>
  <div class="abs" style="left:148px;top:18px;color:var(--white)">
    <span class="line" style="font-size:20px;font-weight:600">Ten-Week</span>
    <span class="line" style="font-size:34px;margin-top:8px">BRIGHT</span>
    <span class="line" style="font-size:28px;color:var(--rose);font-weight:600;margin-top:6px">Morning</span>
  </div>
  <div class="abs" style="right:12px;top:232px;color:var(--white);text-align:right">
    <span class="line" style="font-size:34px">REBOOT</span>
  </div>
</section>

<section class="tile col-2 row-3" style="background:var(--cream)">
  <div class="abs" style="left:0;top:0;width:259px;height:156px;background:var(--forest);text-align:center;padding-top:18px">
    <span class="line" style="font-size:36px;color:var(--rose)">The Quick</span>
    <span class="line" style="font-size:31px;color:var(--white);margin-top:8px">GARDEN KITCHEN</span>
    <span class="bar" style="margin:10px auto 0;width:217px;height:25px;background:var(--rose-mid);color:var(--forest);font-size:21px;letter-spacing:4px;line-height:25px">Menu Guide</span>
  </div>
  <div class="photo" role="img" aria-label="Fresh vegetables, fruit, salmon and chicken framing a meal planner notebook on dark wood" style="left:17px;top:166px;width:225px;height:150px;background:radial-gradient(ellipse at center,#3a2e28 0%,#3a2e28 35%,#8c6a3a 60%,#c23a2a 80%,#4f7a2e 100%)"></div>
</section>

<section class="tile col-3 row-3" style="background:var(--cream)">
  <div class="photo" role="img" aria-label="Two women against a blue backdrop, one whispering a secret to the other" style="left:15px;top:22px;width:228px;height:152px;background:linear-gradient(90deg,#6fc3dc 0%,#dcc2b0 40%,#8a6a58 60%,#6fc3dc 100%)"></div>
  <svg class="blob" style="top:184px;height:130px" viewBox="0 0 259 130" preserveAspectRatio="none" aria-hidden="true">
    <path d="M16 14 L80 2 L140 10 L200 0 L248 12 L240 46 L254 84 L238 120 L180 112 L120 126 L60 114 L14 124 L20 90 L4 56 L18 34 Z" fill="var(--forest)"/>
  </svg>
  <div class="abs" style="left:0;width:259px;top:200px;text-align:center;color:var(--white)">
    <span class="line" style="font-size:20px;font-weight:600">Studio Habits for Lasting</span>
    <span class="line" style="font-size:38px;margin-top:5px">ENERGY PAST</span>
    <span class="line" style="font-size:15px;font-weight:600;margin-top:7px">Midlife - Zero Gym Needed</span>
  </div>
</section>

</body>
</html>
```